Calvera fine stockings - sexy cardboard box design needed!

We need a packaging design for a new online company based in Sydney called 'Calvera Hosiery'. We will be selling sexy stockings to our customers by Italian designers. We mainly feature lace stockings, an example of which, can be seen here:
http://www.brontevassipelli.example/italy-FASHION-WINTER

The design should be a cardboard pull out box, black in colour with the logo on the cover. We are looking for the logo to communicate sophistication and sexiness.

Examples of cardboard box shapes we would like are:
http://www.tradoquel.example/product-gs/583016274/High_quality_drawer_paper_box.html

http://www.tradoquel.example/product-gs/639152487/Cardboard_drawer_box.html

29 December:
I submitted a note when I extended the deadline, but cannot see it, so will write here for clarification. It has been difficult to choose the best design as the designs submitted were of such high quality. I want to have some people judge the designs, but because of the Christmas Season I have extended the deadline so that this can be done. Thanks.

Target Market(s)

The working professional woman.

Industry/Entity Type

Fashion

Requirements
Must have
• The words "Calvera Hosiery" on the cover of the box.

The box should be a sliding drawer.

The box size should be: (22*15*2.5cm).

Washing instructions and recycling logos on the back of the box. See example of uploaded file.

Nice to have
• It would be nice to have the background of the box a dark colour, maybe charcoal? But we are open to all ideas.
Should not have
• A stock photo on cover of box.

```html
<!DOCTYPE html>
<html lang="en">
<head>
<meta charset="utf-8">
<title>Calvera Hosiery – Drawer Box Dieline</title>
<link rel="stylesheet" href="https://fonts.googleapis.com/css2?family=Josefin+Sans:wght@300&display=swap">
<style>
  :root {
    --page: #ffffff;
    --board: #231f20;
    --lace-glow: #5a2a42;
    --lace-base: #2b2226;
    --rule: #e0157f;
    --type: #e9e6e7;
  }
  html, body {
    margin: 0;
    padding: 0;
    width: 1200px;
    height: 849px;
    overflow: hidden;
    background: var(--page);
  }
  .dieline { display: block; width: 1200px; height: 849px; }
  .board { fill: var(--board); }
  .frame { fill: none; stroke: var(--rule); stroke-width: 1; }
  .fold-solid { stroke: var(--rule); stroke-width: 2.5; }
  .fold-dashed { stroke: var(--rule); stroke-width: 1; stroke-dasharray: 5 4; }
  .lace-field { fill: url(#lace-tone); }
  .lace-stop-glow { stop-color: var(--lace-glow); }
  .lace-stop-base { stop-color: var(--lace-base); }
  .brand-name {
    font-family: "Josefin Sans", sans-serif;
    font-weight: 300;
    fill: var(--type);
    text-anchor: middle;
  }
  .brand-dot { fill: var(--rule); }
  .care-icon { fill: none; stroke: var(--type); stroke-width: 1; }
</style>
</head>
<body>
<svg class="dieline" viewBox="0 0 1200 849" xmlns="http://www.w3.org/2000/svg">
  <defs>
    <radialGradient id="lace-tone" cx="50%" cy="50%" r="70%">
      <stop offset="0" class="lace-stop-glow"/>
      <stop offset="1" class="lace-stop-base"/>
    </radialGradient>
  </defs>

  <!-- Board shapes -->
  <rect class="board" x="228" y="156" width="420" height="532"/>
  <rect class="board" x="640" y="96" width="367" height="650"/>

  <!-- Bleed frames -->
  <path class="frame" d="M640 162 H235 V681 H640"/>
  <rect class="frame" x="647" y="103" width="353" height="636"/>

  <!-- Lace pattern fields -->
  <g role="img" aria-label="Pink dashed lace diamond pattern">
    <rect class="lace-field" x="248" y="176" width="324" height="158"/>
    <rect class="lace-field" x="597" y="176" width="36" height="158"/>
    <rect class="lace-field" x="662" y="176" width="323" height="158"/>
    <rect class="lace-field" x="662" y="117" width="323" height="33"/>
    <rect class="lace-field" x="248" y="505" width="324" height="160"/>
    <rect class="lace-field" x="597" y="505" width="36" height="160"/>
    <rect class="lace-field" x="662" y="505" width="323" height="160"/>
    <rect class="lace-field" x="662" y="690" width="323" height="33"/>
  </g>

  <!-- Fold lines -->
  <line class="fold-solid" x1="228" y1="354" x2="1000" y2="354"/>
  <line class="fold-solid" x1="228" y1="482" x2="1000" y2="482"/>
  <line class="fold-dashed" x1="587" y1="162" x2="587" y2="681"/>
  <line class="fold-dashed" x1="647" y1="162" x2="647" y2="681"/>
  <line class="fold-dashed" x1="647" y1="162" x2="1000" y2="162"/>
  <line class="fold-dashed" x1="647" y1="681" x2="1000" y2="681"/>

  <!-- Back panel -->
  <g class="back-panel">
    <text class="brand-name" x="413" y="400" font-size="10" letter-spacing="5">CALVERA</text>
    <circle class="brand-dot" cx="413" cy="412" r="3"/>
    <text class="brand-name" x="413" y="430" font-size="7" letter-spacing="4">HOSIERY</text>
    <g class="care-icons" transform="translate(374 451)">
      <path class="care-icon" d="M0 1 L2 9 H10 L12 1"/>
      <path class="care-icon" d="M16 9 L22 1 L28 9 Z"/>
      <path class="care-icon" d="M33 9 H45 V6 Q45 2 38 2 H35 Z"/>
      <circle class="care-icon" cx="56" cy="5" r="4.5"/>
      <line class="care-icon" x1="52" y1="1" x2="60" y2="9"/>
      <line class="care-icon" x1="60" y1="1" x2="52" y2="9"/>
      <rect class="care-icon" x="66" y="0.5" width="9" height="9"/>
      <circle class="care-icon" cx="70.5" cy="5" r="3"/>
    </g>
  </g>

  <!-- Spine -->
  <text class="brand-name" font-size="6" letter-spacing="3"
        transform="translate(615 418) rotate(90)">CALVERA HOSIERY</text>

  <!-- Cover panel -->
  <g class="cover-panel">
    <text class="brand-name" x="823" y="408" font-size="17" letter-spacing="10">CALVERA</text>
    <circle class="brand-dot" cx="823" cy="424" r="4"/>
    <text class="brand-name" x="823" y="448" font-size="10" letter-spacing="6">HOSIERY</text>
  </g>
</svg>
</body>
</html>
```